Business Card and Letterhead for Pimlu - modern real estate business

I need a double sided business card design for Pimlu. Please see business card brief here https://files.trelvonadocs.com/sheet/r/7QzTmWbaXLJnoPEd-kRyUgFhHsstbvCe2qfoMxDa_pz/view?mode=shared

Please feel free to design the business cards however you feel best. I am happy to give some creative freedoms and then provide feedback from there.

Please then also create a letterhead to match the business card design

Colors

Designer to choose colors to be used in the design.

Requirements
Must have
• Must be a modern, elegant business card which looks very professional

```html
<!DOCTYPE html>
<html lang="en">
<head>
<meta charset="utf-8">
<title>Pimlu – Business Card</title>
<link href="https://fonts.googleapis.com/css2?family=Roboto:wght@400;500;700&display=swap" rel="stylesheet">
<style>
  :root{
    --bg:#2a2a2c;
    --card-dark:#1f1f21;
    --card-light:#ffffff;
    --brand-red:#e4141f;
    --silver:#c9cacc;
    --ink:#2b2b2b;
    --ink-soft:#555555;
    --photo-a:#f1f1f1;
    --photo-b:#4a4c52;
  }
  *{margin:0;padding:0;box-sizing:border-box}
  html,body{width:1200px;height:960px;overflow:hidden}
  body{background:var(--bg);font-family:'Roboto',Arial,sans-serif;position:relative}

  .card{position:absolute;width:600px;height:343px;box-shadow:0 18px 40px rgba(0,0,0,.45)}

  /* back side */
  .card--back{left:80px;top:90px;background:var(--card-dark);display:flex;align-items:center;justify-content:center}
  .card--back .wordmark{color:var(--silver);font-size:72px;font-weight:700;letter-spacing:6px}

  /* front side */
  .card--front{left:520px;top:500px;background:var(--card-light);overflow:hidden}
  .front__info{position:absolute;left:40px;top:40px;width:270px}
  .wordmark{display:block;font-weight:700;text-transform:uppercase;line-height:1}
  .front__info .wordmark{color:var(--brand-red);font-size:52px;letter-spacing:4px}
  .person{margin-top:32px}
  .person__name{color:var(--brand-red);font-size:21px;font-weight:700;line-height:1.2}
  .person__title{color:var(--ink);font-size:14px;font-weight:500;line-height:1.2;margin-top:2px}
  .contacts{list-style:none;margin-top:12px;padding-left:18px;color:var(--ink-soft);font-size:14px;line-height:1.3}
  .contacts li{display:flex;align-items:flex-start;gap:10px}
  .contacts li + li{margin-top:2px}
  .contacts .contact--address{margin-bottom:8px}
  .contacts svg{width:13px;height:13px;flex:none;margin-top:3px;fill:var(--brand-red)}

  .front__photo{position:absolute;right:0;top:0;width:290px;height:314px;
    background:linear-gradient(180deg,var(--photo-a) 0%,var(--photo-a) 25%,var(--photo-b) 100%)}
  .front__band{position:absolute;left:0;right:0;bottom:0;height:25px;background:var(--brand-red)}
  .front__band::before{content:"";position:absolute;left:0;right:0;top:-4px;height:4px;background:var(--card-light)}
</style>
</head>
<body>
  <section class="card card--back" aria-label="Business card back">
    <span class="wordmark">Pimlu</span>
  </section>

  <section class="card card--front" aria-label="Business card front">
    <div class="front__info">
      <span class="wordmark">Pimlu</span>
      <div class="person">
        <p class="person__name">Mara Keller</p>
        <p class="person__title">Licenced Real Estate Agent</p>
      </div>
      <ul class="contacts">
        <li class="contact--address">
          <svg viewBox="0 0 24 24"><path d="M12 2a7 7 0 0 0-7 7c0 5 7 13 7 13s7-8 7-13a7 7 0 0 0-7-7zm0 9.5A2.5 2.5 0 1 1 12 6.5a2.5 2.5 0 0 1 0 5z"/></svg>
          <span>PO Box 1903<br>Larkfield NSW 2690</span>
        </li>
        <li>
          <svg viewBox="0 0 24 24"><path d="M6.6 10.8a15 15 0 0 0 6.6 6.6l2.2-2.2a1 1 0 0 1 1-.25 11.4 11.4 0 0 0 3.6.57 1 1 0 0 1 1 1V20a1 1 0 0 1-1 1A17 17 0 0 1 3 4a1 1 0 0 1 1-1h3.5a1 1 0 0 1 1 1c0 1.25.2 2.45.57 3.6a1 1 0 0 1-.25 1z"/></svg>
          <span>0412 380 519</span>
        </li>
        <li>
          <svg viewBox="0 0 24 24"><path d="M3 5h18v14H3zm2 2v.5l7 4.5 7-4.5V7l-7 4.5z"/></svg>
          <span>mara@pimlu.com</span>
        </li>
        <li>
          <svg viewBox="0 0 24 24"><circle cx="12" cy="12" r="10"/></svg>
          <span>www.pimlu.com</span>
        </li>
      </ul>
    </div>
    <div class="front__photo" role="img" aria-label="Portrait photo of the agent in a dark suit"></div>
    <div class="front__band"></div>
  </section>
</body>
</html>
```